University Social app needs Instagram layout help - tile layout and designs for 18 different types

We need a instagram profile look for our app Tindleloop that is getting a new look and feel. We want 18 different tiles designs that mesh well and look good together on the profile page. This can be a mix of images and text. Tindleloop is based in Sydney, Australia and is a Social app that helps students connect IRL ,find new friends and activities/experiences through society campus events. Topics can include but not limited to the following: Whats on, society spotlight, how to use Tindleloop, Tindleloop features, memes, Helpful hits, POV, Uni Life IRL, Make the Connection, Try Something New, Tindleloop Community, Student Voice, Uni 101, Tindleloop It, Student Stories. please also see current Tindleloop instagram page for content type ideas. It also needs to have the new Tindleloop brand colours (#04ccd9 with a gradient to white background) (also see attached file). The final tiles should communicate university fun, connection and a place to find events. Swap out the current stickers for activity based stickers similar to the attached examples to demonstrate that the app is for finding fun events and activities and for connection.
Look and feel
Each slider illustrates characteristics of the customer's brand and the style your logo design should communicate.

```html
<!DOCTYPE html>
<html lang="en">
<head>
<meta charset="utf-8">
<title>Tindleloop – Profile Tile</title>
<link rel="stylesheet" href="https://fonts.googleapis.com/css2?family=DM+Sans:wght@500;700&display=swap">
<style>
  :root {
    --frame: #333a45;
    --brand-cyan: #5ce3ea;
    --brand-white: #ffffff;
    --ink: #000000;
    --sticker-lime: #d8fb5a;
    --sticker-sky: #62d0f5;
    --sticker-pink: #ff8ad0;
    --sticker-red: #ff5a4c;
    --sticker-orange: #ff9a1a;
    --sticker-yellow: #ffe01a;
    --sticker-green: #28c060;
  }
  html, body {
    margin: 0;
    padding: 0;
    overflow: hidden;
    background: var(--frame);
  }
  .canvas {
    position: relative;
    width: 1200px;
    height: 1200px;
    background: var(--frame);
    overflow: hidden;
  }
  .tile {
    position: absolute;
    left: 125px;
    top: 125px;
    width: 950px;
    height: 950px;
    background: linear-gradient(20deg, var(--brand-cyan) 0%, #b4f1f4 55%, var(--brand-white) 78%);
    overflow: hidden;
  }
  .sticker {
    position: absolute;
  }
  .sticker--spark { left: 280px; top: 292px; width: 110px; height: 112px; border-radius: 20px; background: var(--sticker-lime); }
  .sticker--look { left: 572px; top: 216px; width: 128px; height: 124px; border-radius: 60px; background: linear-gradient(180deg, #ffffff, var(--sticker-sky)); }
  .sticker--greeting { left: 724px; top: 378px; width: 124px; height: 96px; border-radius: 26px; background: linear-gradient(135deg, var(--sticker-pink), var(--sticker-sky)); transform: rotate(-8deg); }
  .sticker--flame { left: 818px; top: 530px; width: 74px; height: 122px; border-radius: 40px 40px 38px 38px; background: linear-gradient(180deg, var(--sticker-red), var(--sticker-yellow)); }
  .sticker--pizza { left: 244px; top: 632px; width: 114px; height: 128px; border-radius: 22px; background: linear-gradient(160deg, var(--sticker-orange), var(--sticker-yellow)); transform: rotate(-10deg); }
  .sticker--melon { left: 436px; top: 808px; width: 122px; height: 128px; border-radius: 22px; background: linear-gradient(180deg, var(--sticker-red), var(--sticker-green)); }
  .brand-name {
    position: absolute;
    left: 0;
    width: 1188px;
    top: 522px;
    margin: 0;
    text-align: center;
    font-family: "DM Sans", sans-serif;
    font-weight: 700;
    font-size: 84px;
    line-height: 1;
    letter-spacing: -1.5px;
    color: var(--ink);
  }
  .site-link {
    position: absolute;
    left: 374px;
    top: 676px;
    width: 444px;
    height: 98px;
    border-radius: 49px;
    background: var(--ink);
    color: var(--brand-white);
    display: flex;
    align-items: center;
    justify-content: center;
    gap: 10px;
    font-family: "DM Sans", sans-serif;
    font-weight: 500;
    font-size: 50px;
    letter-spacing: -0.5px;
    text-decoration: none;
  }
  .site-link__chevron {
    font-size: 34px;
  }
</style>
</head>
<body>
  <main class="canvas">
    <section class="tile"></section>

    <div class="sticker sticker--spark" role="img" aria-label="Lime green asterisk sparkle sticker"></div>
    <div class="sticker sticker--look" role="img" aria-label="Cartoon googly eyes sticker"></div>
    <div class="sticker sticker--greeting" role="img" aria-label="Hand-lettered hi! greeting sticker"></div>
    <div class="sticker sticker--flame" role="img" aria-label="Red and yellow flame sticker"></div>
    <div class="sticker sticker--pizza" role="img" aria-label="Pizza slice sticker"></div>
    <div class="sticker sticker--melon" role="img" aria-label="Smiling watermelon slice sticker"></div>

    <h1 class="brand-name">Tindleloop</h1>
    <a class="site-link" href="#">tindleloop.com<span class="site-link__chevron">›</span></a>
  </main>
</body>
</html>
```